Verpackungsdesign für Wellness- und Saunaprodukte
Zielgruppe
BaFinn ist ein junges Start-Up, das sich auf Wellness- und Saunaprodukte spezialisiert hat. Unsere Zielgruppe besteht zu beinahe gleichen Teilen aus männlichen und weiblichen Personen zwischen 30 und 60 Jahren. Unsere Produkte befinden sich eher im mittel- bis höherpreisigen Segment, daher streben wir ein hochwertiges Design für unsere Verpackungen an. Unsere Produktpalette reicht von Mentholkristallen, Saunaaufgüssen, bis hin zu Textilien für den Wellnessbereich und soll dementsprechend Menschen ansprechen, die sich einen gewissen Luxus im Alltag auch gönnen.
Aufgabenstellung
Inspiriert von der skandinavischen Sauna Kultur, möchten wir Momente der Erholung und
Entspannung in den Alltag unserer Kunden bringen. Die Geschichte des Saunierens ist eng mit der skandinavischen Kultur verbunden und skandinavische Stilelemente sind zeitgemäß und sprechen ein breites Publikum an. Das Design muss auf Dosen/Tiegel , Karton Verpackungen und Flaschen verschiedener Größen adaptierbar sein (siehe Bild im Anhang).
40g Tiegel(transparent) Höhe 40mm Durchmesser 60mm (ohne Deckel Silber gebürstet)
100g Tiegel(transparent) Höhe 53mm Durchmesser 71mm (ohne Deckel Silber gebürstet)
200g Tiegel(transparent) Höhe 65mm Durchmesser 90mm (ohne Deckel Silber gebürstet)
Karton Verpackung 124,5x49x49mm
Karton Verpackung 100x100x100mm
Flaschenetikett 134x67mm (Braunglas, schwarzer Deckel)
Es soll ein passendes Keyvisual erstellt werden.
Im Anhang sieht man die Verpackungen, Dosen, Flaschen sowie unsere ersten Design Entwürfe (an diese Anordnung der Elemente kann sich der Designer orientieren ). Das Logo bleibt wie gegeben. Das Produkt für die Tiegel soll Mentholkristalle sein.

```html
<!DOCTYPE html>
<html lang="de">
<head>
<meta charset="utf-8">
<title>BaFinn – Nordische Fichte</title>
<link rel="stylesheet" href="https://fonts.googleapis.com/css2?family=Montserrat:wght@300;500&family=Alegreya+Sans:wght@400;500&family=Archivo+Narrow:wght@600&display=swap">
<style>
  :root {
    --stage: #eef1ed;
    --side-black: #0c0c0c;
    --side-text: #f2f2f2;
    --sage: #8fa08c;
    --sage-light: #a3b2a0;
    --sage-line: #b7c1b6;
    --navy: #1f2d45;
    --leaf: #6f8a66;
    --leaf-dark: #4f6a4b;
    --tube-body: #d5ddd6;
    --tube-light: #e8ede8;
    --cap: #5f7a67;
    --cap-dark: #465e4e;
  }
  * { margin: 0; padding: 0; box-sizing: border-box; }
  html, body { width: 1200px; height: 1200px; overflow: hidden; }
  body { background: var(--stage); position: relative; font-family: "Montserrat", sans-serif; }

  .box-side {
    position: absolute; left: 70px; top: 200px; width: 270px; height: 780px;
    background: var(--side-black); color: var(--side-text);
    font-family: "Alegreya Sans", sans-serif; padding: 40px 26px 30px;
  }
  .box-side .tab { width: 5px; height: 34px; background: var(--side-text); margin-bottom: 28px; }
  .usage { margin-bottom: 16px; }
  .usage h3 { font-size: 12px; font-weight: 500; text-transform: uppercase; letter-spacing: .02em; margin-bottom: 3px; }
  .usage p { font-size: 10.5px; line-height: 1.35; }
  .imprint { position: absolute; left: 26px; bottom: 34px; font-size: 8.5px; line-height: 1.5; text-transform: uppercase; }
  .imprint .web { text-transform: none; font-size: 10px; margin-top: 6px; }
  .symbols { position: absolute; right: 22px; bottom: 40px; display: flex; flex-direction: column; gap: 10px; align-items: center; }
  .symbols .jar { width: 16px; height: 20px; border: 1.2px solid var(--side-text); border-radius: 2px; }
  .symbols .bin { width: 2px; height: 40px; background: var(--side-text); }

  .box-front {
    position: absolute; left: 340px; top: 200px; width: 440px; height: 780px;
    background: var(--sage); overflow: hidden;
  }
  .front-pattern {
    position: absolute; inset: 0;
    background: linear-gradient(160deg, var(--sage-light) 0%, var(--sage) 55%, #879885 100%);
  }
  .brand { position: absolute; left: 0; right: 0; top: 150px; display: flex; flex-direction: column; align-items: center; gap: 16px; }
  .brand-dot { width: 46px; height: 46px; border-radius: 50%; background: var(--navy); }
  .brand-name { font-family: "Montserrat", sans-serif; font-weight: 500; font-size: 30px; color: var(--navy); }
  .product-name {
    position: absolute; left: 0; right: 0; top: 380px; text-align: center;
    font-weight: 300; font-size: 58px; line-height: 1.15; color: var(--navy);
  }
  .front-botanical {
    position: absolute; right: 0; top: 450px; width: 140px; height: 330px;
    background: linear-gradient(180deg, rgba(111,138,102,0) 0%, var(--leaf) 45%, var(--leaf-dark) 100%);
    opacity: .75; border-top-left-radius: 70px;
  }

  .tube { position: absolute; left: 810px; top: 230px; width: 340px; height: 760px; }
  .tube svg { position: absolute; inset: 0; }
  .tube-brand { position: absolute; left: 0; right: 0; top: 110px; display: flex; flex-direction: column; align-items: center; gap: 12px; }
  .tube-brand .brand-dot { width: 40px; height: 40px; }
  .tube-brand .brand-name { font-size: 27px; }
  .tube-label {
    position: absolute; left: 0; right: 0; top: 290px; text-align: center;
    font-family: "Archivo Narrow", sans-serif; font-weight: 600; font-size: 40px; color: var(--navy); letter-spacing: -.01em;
  }
  .tube-botanical {
    position: absolute; left: 60px; top: 380px; width: 150px; height: 240px;
    background: linear-gradient(200deg, rgba(111,138,102,.15), var(--leaf) 60%, var(--leaf-dark));
    opacity: .7; border-radius: 80px 20px 60px 20px;
  }
</style>
</head>
<body>
  <section class="box-side">
    <div class="tab"></div>
    <div class="usage"><h3>Cooling Shave Cream</h3><p>Apply a thin layer to clean, damp face and neck. Shave as usual.</p></div>
    <div class="usage"><h3>Crème de rasage rafraîchissante</h3><p>Appliquez en couche fine sur le visage et le cou humides, préalablement nettoyés. Rasez comme à votre habitude.</p></div>
    <div class="usage"><h3>Kühlende Rasiercreme</h3><p>Tragen Sie eine dünne Schicht auf die gereinigte, leicht befeuchtete Haut von Gesicht und Hals auf. Anschließend wie gewohnt rasieren.</p></div>
    <div class="usage"><h3>Espuma de afeitar efecto frío</h3><p>Aplicar una fina capa en el cuello y rostro limpios y húmedos. Aféitese como de costumbre.</p></div>
    <div class="usage"><h3>Crema da barba rinfrescante</h3><p>Applicare uno strato sottile su viso e collo puliti e umidi. Radersi come d'abitudine.</p></div>
    <div class="usage"><h3>Koelende scheercrème</h3><p>Breng een dun laagje aan om te reinigen, bevochtig op het gezicht en hals. Scheer zoals gewoonlijk.</p></div>
    <div class="imprint">
      Nordhal Vertrieb, Dist.<br>Hafenstr. 12, Kiel<br>Made in Germany
      <div class="web">nordhal-vertrieb.de</div>
    </div>
    <div class="symbols"><div class="jar"></div><div class="bin"></div></div>
  </section>

  <section class="box-front">
    <div class="front-pattern" role="img" aria-label="Feines Linienmuster aus gestreiften Dreiecken in hellem Salbeigrün"></div>
    <div class="brand"><span class="brand-dot"></span><span class="brand-name">BaFinn</span></div>
    <h1 class="product-name">Nordische<br>Fichte</h1>
    <div class="front-botanical" role="img" aria-label="Aquarell-Zweige mit grünen Blättern am rechten Rand"></div>
  </section>

  <section class="tube">
    <svg width="340" height="760" viewBox="0 0 340 760" role="img" aria-label="Flache Cremetube mit Schraubkappe">
      <defs>
        <linearGradient id="tubeShade" x1="0" x2="1">
          <stop offset="0" stop-color="var(--tube-body)"/>
          <stop offset=".5" stop-color="var(--tube-light)"/>
          <stop offset="1" stop-color="var(--tube-body)"/>
        </linearGradient>
        <linearGradient id="capShade" x1="0" x2="1">
          <stop offset="0" stop-color="var(--cap-dark)"/>
          <stop offset=".5" stop-color="var(--cap)"/>
          <stop offset="1" stop-color="var(--cap-dark)"/>
        </linearGradient>
      </defs>
      <rect x="0" y="0" width="340" height="16" fill="#dfe5df"/>
      <path d="M0 16 H340 L280 620 H60 Z" fill="url(#tubeShade)"/>
      <path d="M60 620 H280 L272 740 Q170 760 68 740 Z" fill="url(#capShade)"/>
    </svg>
    <div class="tube-brand"><span class="brand-dot"></span><span class="brand-name">BaFinn</span></div>
    <div class="tube-label">CREAM TUBE</div>
    <div class="tube-botanical" role="img" aria-label="Aquarell-Zweig mit grünen Blättern"></div>
  </section>
</body>
</html>
```